Stationery Design Project

We need a stationery design for our Norwegian trucking company. We have existed for about 15 years and our 12 drivers uses relatively new vehicles to transport goods around in northern Norway. Long distance routes with fresh fish og food transport is our main operations.

We have already made alogo that's printed on our trucks. The logo and a picture of our trucks is attached. I think the logo i crappy, but since its already in use, changing it is not an option in this round. Still using a better colour scheme in the overall stationery and more interesting fonts is possible (altso in the logo).

Company details:
Name: Kjelvraket AS
Organisation nr 873 615 309
Post adress: 8642 Raudvik

I like minimalism and simplicity. I am avalibly for questions in normal GMT working hours either here or on mail: ivar@fjordlast.no

Reason: Hi. Im extending the deadline because I needed some time to find a vector file of our logo. Sorry for the inconvenience

Hi, and thanks for all your interest in the project. Some updates:

-          I have decided to commit to using one of the designs. Some designer will get the payment.

-          I have extended the deadline with 24 hours since I needed some time to find our firms vector logo (a slow Swedish man was holding me up)

-          We will not choose a design before the deadline. No need to rush.

-          We have received a lot of great design and think there is a need to specified the product we want to make:

o   Business Card for all our employers. I just need the design and will duplicate with the correct numbers and name myself. The information on should be: Logo, employer’s name, Phone number, email, website, Postal number and address. Use this as a template: logo, Leif Brattvoll, 47382066, Leif@fjordlast.no,, fjordlast.no, 8642 Raudvik. The order and placement of the information is your creative decision.

o   Stickers to put on the goods we travel. On the sticker the should be the following information: Logo, phone number, Tekst and link: Fraktæ av Kjelvraket. Ke du syns? Fjordlast.no/tilbakemelding (this means: Handled by Kjelvraket. What do you think Fjordlast.no/feedback -à the link will be a feedback form). The placement the information and size is your creative decision with some stings: we have been thinking of using Drukko for printing and see that a size about 6x6 cm, 8x5 or something like that. (with 3000 copies our budget is 200 punds). Any suggestions of other suppliers are welcome. Drukko price calculator http://www.drukkolabelhouse.co.uk/digital-litho-printing/printing-labels-tags/stickers/

o   Letterhead with logo, address, phone number and organizational number.

o   Envelopes with logo,address, phone number and organizational number.

Have a nice day.

 

 

• Using the blue colour in the logo and using a similar graphic approch.

```html
<!DOCTYPE html>
<html lang="en">
<head>
<meta charset="utf-8">
<title>Kjelvraket – Business Card</title>
<link href="https://fonts.googleapis.com/css2?family=Open+Sans:wght@400;600;700&display=swap" rel="stylesheet">
<style>
  :root {
    --stage: #e6e8ec;
    --card-white: #ffffff;
    --brand-navy: #1f2a78;
    --brand-blue: #1d6fb8;
    --band-blue: #1f5fae;
    --band-blue-dark: #214a9c;
    --band-grey: #8e9196;
    --text-grey: #6d6f73;
    --back-light: #2784b8;
    --back-dark: #22409a;
  }
  * { box-sizing: border-box; margin: 0; padding: 0; }
  html, body { width: 1200px; height: 900px; overflow: hidden; }
  body {
    background: var(--stage);
    font-family: "Open Sans", Arial, sans-serif;
    position: relative;
  }
  .card {
    position: absolute;
    width: 600px;
    height: 343px;
    border-radius: 26px;
    overflow: hidden;
    box-shadow: 0 10px 30px rgba(0,0,0,0.18);
  }
  /* back of card */
  .card-back {
    left: 540px;
    top: 70px;
    background: radial-gradient(ellipse at 45% 62%, var(--back-light) 0%, var(--back-dark) 80%);
    display: flex;
    align-items: center;
    justify-content: center;
  }
  .card-back .brand-name {
    color: var(--card-white);
    font-size: 46px;
    font-weight: 600;
    letter-spacing: 0.5px;
  }
  /* front of card */
  .card-front {
    left: 70px;
    top: 470px;
    background: var(--card-white);
  }
  .card-front .brand-name {
    position: absolute;
    left: 42px;
    top: 34px;
    color: var(--brand-navy);
    font-size: 36px;
    font-weight: 600;
  }
  .holder {
    position: absolute;
    left: 42px;
    top: 140px;
  }
  .holder-name {
    color: var(--brand-blue);
    font-size: 25px;
    font-weight: 700;
    line-height: 1.1;
  }
  .holder-title {
    color: var(--text-grey);
    font-size: 15px;
    margin-top: 3px;
  }
  .contact {
    position: absolute;
    left: 340px;
    top: 112px;
    color: var(--text-grey);
    font-size: 15px;
    line-height: 1.35;
  }
  .contact-address { margin-bottom: 8px; }
  .contact-row {
    display: flex;
    align-items: center;
    gap: 10px;
  }
  .contact-row svg { width: 14px; height: 14px; flex: none; }
  .swoosh {
    position: absolute;
    left: 0;
    bottom: 0;
    width: 600px;
    height: 110px;
  }
</style>
</head>
<body>

  <section class="card card-back" aria-label="Business card, back">
    <span class="brand-name">Kjelvraket</span>
  </section>

  <section class="card card-front" aria-label="Business card, front">
    <span class="brand-name">Kjelvraket</span>

    <div class="holder">
      <p class="holder-name">Jonas Dalberg</p>
      <p class="holder-title">Marketing Manager</p>
    </div>

    <div class="contact">
      <p class="contact-address">418 Harbour Crest Lane,<br>Westvale, WA 6190</p>
      <p class="contact-row">
        <svg viewBox="0 0 14 14" aria-hidden="true"><path d="M1 5 C1 2 13 2 13 5 L10 6 L9 4.5 C8 4 6 4 5 4.5 L4 6 Z M3.5 7 L10.5 7 L12 12 L2 12 Z" fill="var(--brand-blue)"/></svg>
        800-555-0192
      </p>
      <p class="contact-row">
        <svg viewBox="0 0 14 14" aria-hidden="true"><rect x="1" y="9" width="2" height="4" fill="var(--brand-blue)"/><rect x="4.5" y="7" width="2" height="6" fill="var(--brand-blue)"/><rect x="8" y="4.5" width="2" height="8.5" fill="var(--brand-blue)"/><rect x="11.5" y="2" width="2" height="11" fill="var(--brand-blue)"/></svg>
        0404 555 318
      </p>
      <p class="contact-row">
        <svg viewBox="0 0 14 14" aria-hidden="true"><rect x="1" y="3" width="12" height="8" fill="none" stroke="var(--brand-blue)" stroke-width="1.2"/><path d="M1 3 L7 8 L13 3" fill="none" stroke="var(--brand-blue)" stroke-width="1.2"/></svg>
        jonas@fjordlast.com
      </p>
      <p class="contact-row">
        <svg viewBox="0 0 14 14" aria-hidden="true"><circle cx="7" cy="7" r="6" fill="none" stroke="var(--brand-blue)" stroke-width="1.3"/><ellipse cx="7" cy="7" rx="2.6" ry="6" fill="none" stroke="var(--brand-blue)" stroke-width="1.1"/><path d="M1 7 H13" stroke="var(--brand-blue)" stroke-width="1.1"/></svg>
        www.fjordlast.com
      </p>
    </div>

    <svg class="swoosh" viewBox="0 0 600 110" preserveAspectRatio="none" aria-hidden="true">
      <defs>
        <linearGradient id="bandBlue" x1="0" y1="0" x2="1" y2="0">
          <stop offset="0" stop-color="var(--band-blue)"/>
          <stop offset="0.5" stop-color="#2a86c4"/>
          <stop offset="1" stop-color="var(--band-blue-dark)"/>
        </linearGradient>
      </defs>
      <path d="M0 0 C160 30 360 78 600 86 L600 110 L0 110 Z" fill="var(--band-grey)"/>
      <path d="M0 14 C160 44 360 88 600 94 L600 110 L0 110 Z" fill="url(#bandBlue)"/>
      <path d="M110 34 C250 70 420 92 600 97" fill="none" stroke="#ffffff" stroke-width="2" opacity="0.7"/>
    </svg>
  </section>

</body>
</html>
```